Business Cards Needed for Innovative Healthcare Marketing Company

We are a marketing company focused on healthcare. Our company is all about rebranding yourself renewing your image and generating results. The phoenix stands for "reborn" or "rising" which we provide new brands for our clients we take their old brands and renew it with creativity and innovation. I am looking for a business card with color dimension. I have attached an example of a card I think has the look and feel of what I am trying to accomplish. I like that the card example has black and grey font colors, I like the font placement and the small logo, I really like the use of the colors on the right those are the colors of my logo. My logo is phoenix so maybe incorporating flames similar to that design. I would like the back a solid color maybe red with an opaque version of the logo and website. As a marketing company I am always open to creative liberty!

Target Market(s)

Doctors and business professionals.

Industry/Entity Type

Marketing

Contact Information for Business Card

Valcorne Health Care Marketing
Marla Tenwick- CEO
#(512)638-2974
email-marla@valcorne.com
website- valcorne.com

Font styles to use
Sans Serif

Colors
ec1f27
f37122
ffc214
fbed22
fbf289
f04a50

Requirements
Must have
• The logo and required information
Nice to have
• icons by the information
Should not have
• child like font

```html
<!DOCTYPE html>
<html lang="en">
<head>
<meta charset="utf-8">
<title>Valcorne Health Care Marketing – Business Cards</title>
<link href="https://fonts.googleapis.com/css2?family=Raleway:wght@200;300;400&family=Roboto+Slab:wght@400;700&display=swap" rel="stylesheet">
<style>
  :root {
    --page-bg: #2a1612;
    --card-light: #6e1a22;
    --card-mid: #4a0f16;
    --card-dark: #2a070b;
    --ink-white: #f4eeee;
    --ink-grey: #a9a0a0;
    --ink-soft: #cfc6c6;
    --accent-red: #ec1f27;
    --accent-rose: #f04a50;
    --accent-orange: #f37122;
    --icon-bg: #b3121b;
    --mark-dark: #1c1214;
  }
  * { margin: 0; padding: 0; box-sizing: border-box; }
  html, body { width: 1200px; height: 913px; overflow: hidden; }
  body {
    background: var(--page-bg);
    position: relative;
    font-family: "Raleway", sans-serif;
  }
  .card {
    position: absolute;
    width: 540px;
    height: 309px;
    border-radius: 3px;
    background: radial-gradient(ellipse at 62% 28%, var(--card-light) 0%, var(--card-mid) 50%, var(--card-dark) 100%);
    box-shadow: 0 14px 30px rgba(0,0,0,0.55);
    overflow: hidden;
  }
  .card--front { left: 40px; top: 150px; }
  .card--back  { left: 620px; top: 454px; }

  /* Front */
  .front-mark {
    position: absolute;
    left: 52px; top: 88px;
    width: 130px; height: 130px;
    border-radius: 50%;
    background: var(--mark-dark);
    opacity: 0.85;
  }
  .brand {
    position: absolute;
    left: 214px; top: 100px;
    color: var(--ink-white);
  }
  .brand__name {
    font-family: "Raleway", sans-serif;
    font-weight: 200;
    font-size: 56px;
    letter-spacing: 3px;
    line-height: 1;
  }
  .brand__rule {
    height: 1px;
    width: 290px;
    background: var(--ink-grey);
    margin: 8px 0 6px;
  }
  .brand__tagline {
    font-weight: 300;
    font-size: 15px;
    letter-spacing: 2.2px;
    color: var(--ink-soft);
  }
  .website {
    position: absolute;
    left: 300px; top: 222px;
    font-family: "Roboto Slab", serif;
    font-size: 20px;
    color: var(--ink-soft);
  }
  .website__domain { color: var(--accent-red); }

  /* Back */
  .back-brand {
    position: absolute;
    left: 46px; top: 190px;
    display: flex; align-items: center; gap: 12px;
  }
  .back-brand__mark {
    width: 34px; height: 34px;
    border-radius: 50%;
    background: var(--accent-orange);
  }
  .back-brand__name {
    font-weight: 200;
    font-size: 32px;
    letter-spacing: 2px;
    color: var(--accent-rose);
    line-height: 1;
  }
  .back-brand__tagline {
    position: absolute;
    left: 92px; top: 232px;
    font-weight: 300;
    font-size: 9px;
    letter-spacing: 1.4px;
    color: var(--accent-rose);
    border-top: 1px solid var(--accent-rose);
    padding-top: 3px;
    width: 150px;
  }
  .person {
    position: absolute;
    left: 262px; top: 70px;
    font-family: "Roboto Slab", serif;
  }
  .person__name {
    font-weight: 700;
    font-size: 24px;
    color: var(--ink-white);
  }
  .person__name .surname { text-transform: uppercase; }
  .person__role {
    font-size: 17px;
    color: var(--ink-grey);
    margin-top: -2px;
  }
  .contact {
    list-style: none;
    margin-top: 10px;
  }
  .contact__item {
    display: flex; align-items: center; gap: 10px;
    font-size: 17px;
    color: var(--ink-soft);
    margin-bottom: 6px;
  }
  .contact__icon {
    width: 22px; height: 22px;
    border-radius: 50%;
    background: var(--icon-bg);
    display: flex; align-items: center; justify-content: center;
    flex-shrink: 0;
  }
</style>
</head>
<body>

  <section class="card card--front" aria-label="Card front">
    <div class="front-mark" aria-hidden="true"></div>
    <div class="brand">
      <div class="brand__name">VALCORNE</div>
      <div class="brand__rule"></div>
      <div class="brand__tagline">HEALTH CARE MARKETING</div>
    </div>
    <div class="website">www.<span class="website__domain">valcorne</span>.com</div>
  </section>

  <section class="card card--back" aria-label="Card back">
    <div class="person">
      <div class="person__name">Marla <span class="surname">Tenwick</span></div>
      <div class="person__role">CEO</div>
      <ul class="contact">
        <li class="contact__item">
          <span class="contact__icon">
            <svg width="12" height="12" viewBox="0 0 24 24" aria-hidden="true"><path fill="#f4eeee" d="M6.6 10.8c1.4 2.8 3.8 5.1 6.6 6.6l2.2-2.2c.3-.3.7-.4 1-.2 1.1.4 2.3.6 3.6.6.6 0 1 .4 1 1V20c0 .6-.4 1-1 1C10.6 21 3 13.4 3 4c0-.6.4-1 1-1h3.5c.6 0 1 .4 1 1 0 1.3.2 2.5.6 3.6.1.3 0 .7-.2 1L6.6 10.8z"/></svg>
          </span>
          (512) 638-2974
        </li>
        <li class="contact__item">
          <span class="contact__icon">
            <svg width="12" height="12" viewBox="0 0 24 24" aria-hidden="true"><path fill="#f4eeee" d="M3 5h18v14H3z"/><path fill="none" stroke="#b3121b" stroke-width="2" d="M3 6l9 7 9-7"/></svg>
          </span>
          marla@valcorne.com
        </li>
      </ul>
    </div>
    <div class="back-brand">
      <span class="back-brand__mark" aria-hidden="true"></span>
      <span class="back-brand__name">VALCORNE</span>
    </div>
    <div class="back-brand__tagline">HEALTH CARE MARKETING</div>
  </section>

</body>
</html>
```